ultra-minimalist business card

front (black background, matte):

reza t. kovin
writer | photographer
get@rezakovin.com

back (white background, matte):

a picture speaks a thousand words;
a word draws a thousand pictures.

www.rezakovin.com

all text should be small (white or silver - as long as it shows against the black - on the front; black or gray - as long as it shows against the white - on the back).

feel free to get creative in terms of arrangement, alignment, and font type, but remember, the overall style is minimalist, so nothing too fancy, please.

thanks.

```html
<!DOCTYPE html>
<html lang="en">
<head>
<meta charset="utf-8">
<title>Reza T. Kovin — Business Card</title>
<link rel="stylesheet" href="https://fonts.googleapis.com/css2?family=Lora:wght@500&family=Quicksand:wght@300;400&display=swap">
<style>
  :root {
    --canvas-top: #9a9a9a;
    --canvas-bottom: #cfcfcf;
    --card-white: #f4f4f4;
    --card-black: #1b1c1e;
    --ink-dark: #1a1a1a;
    --ink-gray: #7a7a7a;
    --ink-silver: #d9d9d9;
    --ink-silver-dim: #9c9c9c;
  }
  * { margin: 0; padding: 0; box-sizing: border-box; }
  html, body {
    width: 1200px;
    height: 1200px;
    overflow: hidden;
  }
  body {
    background: linear-gradient(180deg, var(--canvas-top), var(--canvas-bottom));
    display: flex;
    flex-direction: column;
    align-items: center;
    justify-content: center;
    gap: 60px;
  }
  .card {
    position: relative;
    width: 840px;
    height: 480px;
    box-shadow: 0 12px 30px rgba(0, 0, 0, 0.25);
  }
  .name {
    font-family: "Lora", serif;
    font-weight: 500;
    text-transform: uppercase;
    letter-spacing: 3px;
    line-height: 1;
    white-space: nowrap;
  }
  .small-text {
    font-family: "Quicksand", sans-serif;
    font-weight: 300;
    letter-spacing: 0.5px;
    white-space: nowrap;
  }

  /* Back: white */
  .card--back { background: var(--card-white); }
  .card--back .name {
    position: absolute;
    left: 140px;
    top: 190px;
    font-size: 40px;
    color: var(--ink-dark);
  }
  .card--back .website {
    position: absolute;
    left: 330px;
    top: 252px;
    font-size: 17px;
    color: var(--ink-gray);
  }
  .card--back .tagline {
    position: absolute;
    left: 60px;
    bottom: 70px;
    font-size: 17px;
    line-height: 1.6;
    color: var(--ink-gray);
  }

  /* Front: black */
  .card--front { background: var(--card-black); }
  .card--front .identity {
    position: absolute;
    left: 70px;
    top: 200px;
  }
  .card--front .name {
    font-size: 30px;
    color: var(--ink-silver);
  }
  .card--front .role {
    margin-top: 8px;
    font-size: 16px;
    color: var(--ink-silver-dim);
  }
  .card--front .divider {
    position: absolute;
    left: 470px;
    top: 60px;
    width: 2px;
    height: 360px;
    background: var(--ink-silver);
  }
  .card--front .email {
    position: absolute;
    left: 500px;
    bottom: 80px;
    font-size: 20px;
    color: var(--ink-silver);
  }
</style>
</head>
<body>
  <section class="card card--back" aria-label="Card back">
    <h2 class="name">Reza T. Kovin</h2>
    <p class="website small-text">www.rezakovin.com</p>
    <p class="tagline small-text">a picture speaks a thousand words;<br>a word draws a thousand pictures.</p>
  </section>

  <section class="card card--front" aria-label="Card front">
    <div class="identity">
      <h1 class="name">Reza T. Kovin</h1>
      <p class="role small-text">writer | photographer</p>
    </div>
    <div class="divider"></div>
    <p class="email small-text">get@rezakovin.com</p>
  </section>
</body>
</html>
```